Flyer für Immobilienmakler
Zielgruppe
Wir, die Kessler Immobilien GmbH, vermitteln Häuser, Wohnungen und Grundstücke, unsere Zielgruppe sind Verkäufer und Kaufinteressenten aus der Region, Immobilien zur Vermittlung gesucht
Aufgabenstellung
Unverbindliche Ersteinschätzung, Ansprechpartner vor Ort, regionale Marktkenntnis. Max. Din A 5, Immobilien zur Vermittlung gesucht.
- Flyer nur zur Immobilienvermittlung

```html
<!DOCTYPE html>
<html lang="de">
<head>
<meta charset="utf-8">
<title>Kessler Immobilien GmbH – Flyer Immobilienvermittlung</title>
<link rel="stylesheet" href="https://fonts.googleapis.com/css2?family=Noto+Serif:wght@400;600;700&display=swap">
<style>
  :root {
    --stage: #7a7a7a;
    --paper: #ffffff;
    --purple: #6e59a5;
    --sky-top: #3b7fc2;
    --sky-low: #6ea3d6;
    --door-light: #eef0f1;
    --door-shade: #c9d3de;
    --green: #13a37f;
    --ink: #222428;
    --body: #555a60;
    --chevron: #6e59a5;
  }
  * { box-sizing: border-box; margin: 0; padding: 0; }
  html, body { width: 710px; height: 1200px; overflow: hidden; }
  body {
    background: var(--stage);
    font-family: "Noto Serif", Georgia, serif;
    position: relative;
  }
  .flyer {
    position: absolute;
    left: 30px; top: 140px;
    width: 650px; height: 920px;
    background: var(--paper);
    overflow: hidden;
    box-shadow: 0 6px 18px rgba(0,0,0,.35);
  }
  .header {
    position: absolute; left: 0; top: 0; width: 431px; height: 128px;
    background: var(--purple);
    padding: 30px 0 0 38px;
  }
  .header h1 {
    color: #fff; font-weight: 600; font-size: 28px; line-height: 35px;
  }
  .brand {
    position: absolute; left: 431px; top: 0; width: 219px; height: 128px;
    background: var(--sky-top);
    display: flex; align-items: center; justify-content: center; gap: 8px;
  }
  .brand-square { width: 10px; height: 10px; background: #fff; }
  .brand-name { color: #fff; font-size: 13px; font-weight: 400; }
  .house-photo {
    position: absolute; left: 357px; top: 128px; width: 293px; height: 392px;
    background: linear-gradient(180deg, var(--sky-top) 0%, var(--sky-low) 100%);
  }
  .door-photo {
    position: absolute; left: 0; top: 520px; width: 300px; height: 400px;
    background: linear-gradient(90deg, var(--door-shade) 0%, var(--door-light) 100%);
  }
  .intro {
    position: absolute; left: 0; top: 128px; width: 357px; height: 392px;
    padding-right: 26px;
  }
  .why {
    position: absolute; left: 300px; top: 520px; width: 350px; height: 302px;
    background: var(--paper);
  }
  .block { position: relative; padding-left: 38px; }
  .block::before {
    content: ""; position: absolute; left: 0; top: 5px;
    width: 30px; height: 13px; background: var(--green);
  }
  .why .block { padding-left: 32px; }
  .why .block::before { width: 24px; }
  h2 { font-size: 16.5px; font-weight: 600; color: var(--ink); line-height: 20px; }
  .why .search h2 { max-width: 250px; }
  h3 { font-size: 13px; font-weight: 600; color: var(--ink); margin-top: 8px; }
  p { font-size: 11.6px; line-height: 15.5px; color: var(--body); margin-top: 8px; }
  .intro .block:first-child { margin-top: 32px; }
  .intro .block + .block { margin-top: 26px; }
  .intro h3 + p { margin-top: 6px; }
  .why .block:first-child { margin-top: 26px; }
  .why .block + .block { margin-top: 22px; }
  ul { list-style: none; margin-top: 4px; }
  li {
    position: relative; font-size: 11.6px; line-height: 15px; color: var(--body);
    padding-left: 26px; margin-top: 4px; width: 290px;
  }
  li svg { position: absolute; left: 8px; top: 4px; }
  .why p { margin-top: 6px; }
  .why ul { margin-top: 1px; }
  .why .search li { margin-top: 2px; }
  .contact {
    position: absolute; left: 205px; top: 822px; width: 445px; height: 98px;
    background: var(--green); color: #fff; padding: 20px 34px 0 18px;
  }
  .contact-title { display: flex; align-items: center; gap: 12px; }
  .contact-title h2 { color: #fff; font-weight: 400; font-size: 16px; }
  .contact-title span { flex: 1; height: 1px; background: #fff; }
  .contact-cols { display: flex; margin-top: 8px; font-size: 11.3px; line-height: 15px; }
  .contact-cols .address { width: 198px; }
  .contact-cols strong { font-weight: 700; }
</style>
</head>
<body>
<main class="flyer">
  <header class="header">
    <h1>Ihr Regionaler Partner für Immobilienvermittlung</h1>
  </header>
  <div class="brand">
    <span class="brand-square"></span>
    <span class="brand-name">Kessler Immobilien GmbH</span>
  </div>

  <div class="house-photo" role="img" aria-label="Foto: Landhaus mit Garten und Pool unter blauem Himmel"></div>
  <div class="door-photo" role="img" aria-label="Foto: Türklinke mit Schlüssel und Hausanhänger im Schloss"></div>

  <section class="intro">
    <div class="block">
      <h2>Kompetente Immobilienlösungen Vor Ort</h2>
      <p>Die Kessler Immobilien GmbH mit Sitz in Birkenau ist Ihr zuverlässiger Ansprechpartner rund um die Vermittlung von Immobilien.</p>
      <p>Mit fundierter regionaler Marktkenntnis und persönlicher Betreuung unterstützen wir Eigentümer, Käufer, Verkäufer sowie Mietinteressenten.</p>
    </div>
    <div class="block">
      <h2>Unsere Leistung</h2>
      <h3>Immobilienvermittlung</h3>
      <p>Ob Verkauf oder Vermietung – wir kümmern uns zuverlässig um die Vermittlung von Häusern, Wohnungen, Grundstücken und Gebäuden.</p>
      <p>Dabei begleiten wir Sie persönlich von der unverbindlichen Ersteinschätzung bis zum erfolgreichen Abschluss.</p>
    </div>
  </section>

  <section class="why">
    <div class="block">
      <h2>Warum Kessler Immobilien?</h2>
      <ul>
        <li><svg width="10" height="8" viewBox="0 0 10 8"><path d="M1 1l3 3-3 3M5 1l3 3-3 3" fill="none" stroke="var(--chevron)" stroke-width="1.5"/></svg>Persönlicher Ansprechpartner vor Ort</li>
        <li><svg width="10" height="8" viewBox="0 0 10 8"><path d="M1 1l3 3-3 3M5 1l3 3-3 3" fill="none" stroke="var(--chevron)" stroke-width="1.5"/></svg>Umfassende regionale Marktkenntnis</li>
        <li><svg width="10" height="8" viewBox="0 0 10 8"><path d="M1 1l3 3-3 3M5 1l3 3-3 3" fill="none" stroke="var(--chevron)" stroke-width="1.5"/></svg>Transparente und professionelle Abwicklung</li>
        <li><svg width="10" height="8" viewBox="0 0 10 8"><path d="M1 1l3 3-3 3M5 1l3 3-3 3" fill="none" stroke="var(--chevron)" stroke-width="1.5"/></svg>Zuverlässiger Partner für Eigentümer und Investoren</li>
      </ul>
    </div>
    <div class="block search">
      <h2>Immobilien Zur Vermittlung Gesucht</h2>
      <p>Wir sind laufend auf der Suche nach:</p>
      <ul>
        <li><svg width="10" height="8" viewBox="0 0 10 8"><path d="M1 1l3 3-3 3M5 1l3 3-3 3" fill="none" stroke="var(--chevron)" stroke-width="1.5"/></svg>Häusern</li>
        <li><svg width="10" height="8" viewBox="0 0 10 8"><path d="M1 1l3 3-3 3M5 1l3 3-3 3" fill="none" stroke="var(--chevron)" stroke-width="1.5"/></svg>Wohnungen</li>
        <li><svg width="10" height="8" viewBox="0 0 10 8"><path d="M1 1l3 3-3 3M5 1l3 3-3 3" fill="none" stroke="var(--chevron)" stroke-width="1.5"/></svg>Grundstücken</li>
      </ul>
    </div>
  </section>

  <footer class="contact">
    <div class="contact-title"><h2>KONTAKT</h2><span></span></div>
    <div class="contact-cols">
      <div class="address">
        <strong>KESSLER IMMOBILIEN GMBH</strong><br>
        Lindenweg 8,<br>
        84399 Birkenau
      </div>
      <div class="reach">
        <strong>T</strong>: +49 85 00 123450-0<br>
        <strong>E</strong>: info@kessler-birkenau.de
      </div>
    </div>
  </footer>
</main>
</body>
</html>
```